Business card design for new eCommerce site focusing on integrity and strong businsess tactics

We need a business card that will stand out and be memorable. Something with color that matches our company logo colors. Think high end version of Pactivo. There are 2 logos provided. The parent company is called Amber Ledge Partners and we are presenting a new and very exciting eCommerce site called BrightHarborTrade.example.

Target Market(s)

Our target markets are in the Activities, Food and Beverage, Health and Beauty

Industry/Entity Type

Marketing

Contact Information for Business Card

We have 4 members that need cards...I will provide all info to the winner of the design contest
Business Address is
4870 West 63rd Avenue, Suite C207
Phoenix AZ 85731

Font styles to use
Serif
Sans Serif

Colors

Designer to choose colors to be used in the design.

Requirements
Must have
• The card must be memorable...should be unique in design but must exude integrity and be playful .
• I have provided several colors or our parent company...please feel free to use which ever
Nice to have
• I will leave this up to you. Feel free to use other images of your choosing that wraps around our client.....Activities, Dining, Health, Beauty
Should not have
• just dont be boring

```html
<!DOCTYPE html>
<html lang="en">
<head>
<meta charset="utf-8">
<title>BrightHarborTrade.example – Business Card</title>
<link rel="stylesheet" href="https://fonts.googleapis.com/css2?family=Jost:wght@400;500;600&display=swap">
<style>
  :root {
    --backdrop: #2b2b2b;
    --blue-light: #3fbcd6;
    --blue-deep: #2b7db3;
    --blue-mid: #2e86bb;
    --green: #9dc83e;
    --green-bright: #a9cc45;
    --white: #ffffff;
    --paper: #f3f3f3;
    --ink-blue: #2f7fb8;
  }
  * { margin: 0; padding: 0; box-sizing: border-box; }
  html, body { width: 1200px; height: 960px; overflow: hidden; }
  body {
    background: var(--backdrop);
    font-family: "Jost", "Futura", Arial, sans-serif;
    position: relative;
  }
  .card {
    position: absolute;
    width: 600px;
    height: 342px;
    border-radius: 22px;
    overflow: hidden;
  }
  .card-front { left: 302px; top: 131px; background: var(--paper); }
  .card-back {
    left: 299px; top: 490px;
    background: linear-gradient(135deg, var(--blue-light) 0%, var(--blue-mid) 38%, var(--blue-deep) 100%);
  }
  .front-shapes { position: absolute; inset: 0; }
  .contact {
    position: absolute;
    left: 32px;
    top: 70px;
    color: var(--white);
  }
  .contact-name {
    color: var(--green);
    font-size: 22px;
    font-weight: 500;
    letter-spacing: -0.2px;
    line-height: 1.1;
  }
  .contact-role { font-size: 15px; line-height: 1.2; margin-top: 2px; }
  .contact-address { font-size: 14px; line-height: 18px; margin-top: 13px; }
  .contact-lines { list-style: none; margin-top: 11px; font-size: 14px; line-height: 19.5px; }
  .contact-lines li { display: flex; align-items: center; gap: 7px; }
  .contact-lines svg { width: 13px; height: 13px; flex: none; }
  .brand-lockup {
    position: absolute;
    left: 298px;
    top: 154px;
    display: flex;
    align-items: center;
    gap: 9px;
  }
  .brand-dot { width: 20px; height: 20px; border-radius: 50%; background: var(--green); }
  .brand-name { color: var(--ink-blue); font-size: 19px; font-weight: 500; }
  .back-mark {
    position: absolute;
    left: 228px; top: 65px;
    width: 146px; height: 146px;
    border-radius: 50%;
    background: var(--green-bright);
  }
  .back-name {
    position: absolute;
    left: 0; right: 0; top: 222px;
    text-align: center;
    color: var(--green-bright);
    font-size: 34px;
    font-weight: 600;
  }
</style>
</head>
<body>
  <section class="card card-front">
    <svg class="front-shapes" viewBox="0 0 600 342" aria-hidden="true">
      <defs>
        <linearGradient id="frontBlue" x1="0" y1="0" x2="1" y2="1">
          <stop offset="0" stop-color="#3fbcd6"/>
          <stop offset="0.4" stop-color="#2e86bb"/>
          <stop offset="1" stop-color="#2b7db3"/>
        </linearGradient>
      </defs>
      <path d="M0 0 H312 C262 80 235 220 296 342 H0 Z" fill="#2e86bb"/>
      <path d="M0 0 H300 C252 80 228 220 290 342 H0 Z" fill="#ffffff"/>
      <path d="M0 0 H292 C244 80 222 220 282 342 H0 Z" fill="url(#frontBlue)"/>
    </svg>
    <div class="contact">
      <h1 class="contact-name">DANA WHITFIELD</h1>
      <p class="contact-role">CEO/FOUNDER</p>
      <p class="contact-address">4870 West 63rd Avenue<br>Suite C207<br>Phoenix AZ 85731</p>
      <ul class="contact-lines">
        <li><svg viewBox="0 0 16 16"><path fill="#9dc83e" d="M3.5 1.5l2.5 0 1.2 3.2-1.6 1.2c.8 1.8 2.2 3.2 4 4l1.2-1.6 3.2 1.2v2.5c0 .9-.8 1.6-1.7 1.5C6.6 13.1 2.9 9.4 2 3.2 1.9 2.3 2.6 1.5 3.5 1.5z"/></svg>602 555 0148</li>
        <li><svg viewBox="0 0 16 16"><rect x="4" y="0.8" width="8" height="14.4" rx="1.5" fill="none" stroke="#9dc83e" stroke-width="1.6"/><circle cx="8" cy="12.6" r="0.9" fill="#9dc83e"/></svg>602 555 0193</li>
        <li><svg viewBox="0 0 16 16"><rect x="1" y="3.5" width="14" height="9.5" rx="1" fill="#9dc83e"/><path d="M1.5 4.2 8 9l6.5-4.8" fill="none" stroke="#2e86bb" stroke-width="1.2"/></svg>dana@bhtrade.example</li>
        <li><svg viewBox="0 0 16 16"><circle cx="8" cy="8" r="7" fill="#9dc83e"/><path d="M1 8h14M8 1c-3 3.5-3 10.5 0 14M8 1c3 3.5 3 10.5 0 14" fill="none" stroke="#2e86bb" stroke-width="1"/></svg>www.bhtrade.example</li>
      </ul>
    </div>
    <div class="brand-lockup">
      <span class="brand-dot"></span>
      <span class="brand-name">BrightHarborTrade.example</span>
    </div>
  </section>

  <section class="card card-back">
    <span class="back-mark"></span>
    <p class="back-name">Amber Ledge Partners</p>
  </section>
</body>
</html>
```